Dietitian needs awesome business card

I need a contemporary design that's eye catching but professional.
My card is to given to doctors, specialists and patients alike.
I manage patients with chronic diseases
I have uploaded my logo and current business card, I would also like the other Certified Clinical Nutritionist logo incorporated into the design

Target Market(s)

Doctors, specialists and patients

Industry/Entity Type

Healthcare

Contact Information for Business Card

www.brightfieldnutrition.com.au
Ph: 0427 561 903
Fax: 6457 2183
email: marcus.k.diet@fernmail.com
Space on the back of the card with: Appointment date, Appointment time and appointment location

Font styles to use
Serif

Colors
fbee3e
876aae
ffc214

Requirements
Must have
• My Logo
• Certified Clinical Nutritionist Logo
• My 4 locations - Pinebrook Medical Centre, North Corrin Health, Hollis Medical, Ashcombe Doctors Surgery
Nice to have
• I like the colours in my current business card

```html
<!DOCTYPE html>
<html lang="en">
<head>
<meta charset="utf-8">
<title>Brightfield Nutrition &amp; Dietetics – Business Card</title>
<link href="https://fonts.googleapis.com/css2?family=Open+Sans:wght@300;400;600;700&display=swap" rel="stylesheet">
<style>
  :root {
    --green: #a5c91c;
    --blue: #1b4f9c;
    --blue-soft: #3c6fb8;
    --paper: #f6f7f6;
    --paper-shade: #e9ebea;
    --bg: #ecece8;
  }
  html, body {
    margin: 0;
    width: 1200px;
    height: 1023px;
    overflow: hidden;
    background: var(--bg);
    font-family: "Open Sans", Arial, sans-serif;
  }
  .card {
    position: absolute;
    left: 240px;
    width: 720px;
    height: 440px;
    border-radius: 18px;
    overflow: hidden;
    background: linear-gradient(135deg, var(--paper-shade) 0%, #fff 45%, var(--paper) 100%);
    box-shadow: 0 6px 18px rgba(0,0,0,.12);
  }
  .card--front { top: 50px; }
  .card--back { top: 533px; }
  .card__bands { position: absolute; inset: 0; width: 100%; height: 100%; }

  .brand { position: absolute; display: flex; align-items: center; gap: 14px; }
  .brand__dot { width: 58px; height: 58px; border-radius: 50%; background: var(--blue); flex: none; }
  .brand__name { font-weight: 300; color: var(--blue); font-size: 44px; line-height: 1; letter-spacing: .5px; }
  .brand__sub { font-weight: 300; color: var(--blue); font-size: 17px; margin-top: 4px; }

  .divider { position: absolute; height: 1px; background: var(--blue-soft); }

  .front__decor {
    position: absolute; right: 70px; top: 30px;
    width: 210px; height: 210px; border-radius: 50%;
    background: radial-gradient(circle at 40% 45%, #e3e9f1 0%, #edf3df 60%, rgba(255,255,255,0) 72%);
  }
  .person { position: absolute; left: 70px; top: 186px; }
  .person__name { font-size: 31px; font-weight: 600; color: var(--blue); margin: 0; line-height: 1.2; }
  .person__title { font-size: 21px; font-weight: 400; color: var(--green); margin: 2px 0 0; }

  .contacts { position: absolute; left: 70px; top: 290px; margin: 0; padding: 0; list-style: none; }
  .contacts li { display: flex; align-items: center; gap: 12px; font-size: 15px; color: var(--blue); height: 27px; }
  .contacts svg { width: 16px; height: 16px; flex: none; }
  .contacts__label { color: var(--green); font-weight: 600; width: 26px; }

  .locations { position: absolute; left: 420px; top: 290px; }
  .locations__title { margin: 0 0 4px; font-size: 14px; font-weight: 600; color: var(--green); letter-spacing: 1px; text-transform: uppercase; }
  .locations__list { margin: 0; padding: 0; list-style: none; }
  .locations__list li { display: flex; align-items: center; gap: 8px; font-size: 14px; color: var(--blue); height: 23px; }
  .locations__list svg { width: 11px; height: 14px; flex: none; }

  .back__label { position: absolute; right: 110px; top: 120px; font-size: 24px; color: var(--blue); font-weight: 400; }
  .fields { position: absolute; left: 90px; right: 110px; top: 186px; }
  .field { display: flex; align-items: flex-end; gap: 10px; height: 50px; font-size: 15px; color: var(--blue); }
  .field__line { flex: 1; border-bottom: 1px solid var(--green); height: 20px; }
</style>
</head>
<body>

<article class="card card--front">
  <svg class="card__bands" viewBox="0 0 720 440" preserveAspectRatio="none" aria-hidden="true">
    <path d="M0 0 H720 V8 Q340 18 0 74 Z" fill="var(--green)"/>
    <path d="M0 330 Q20 360 60 440 H0 Z" fill="var(--blue)"/>
    <path d="M0 300 Q30 350 80 440 H60 Q24 366 0 330 Z" fill="var(--green)"/>
    <path d="M720 40 Q700 90 640 180 Q690 110 720 70 Z" fill="var(--blue)"/>
    <path d="M720 440 H580 Q670 425 720 360 Z" fill="var(--green)"/>
  </svg>

  <div class="front__decor" role="img" aria-label="Faint large brand mark decoration"></div>

  <div class="brand" style="left:40px; top:60px;">
    <span class="brand__dot"></span>
    <div>
      <div class="brand__name">Brightfield</div>
      <div class="brand__sub">Nutrition &amp; Dietetics</div>
    </div>
  </div>

  <div class="divider" style="left:30px; top:172px; width:420px;"></div>

  <div class="person">
    <h1 class="person__name">Marcus Kellerton</h1>
    <p class="person__title">Certified Clinical Nutritionist</p>
  </div>

  <ul class="contacts">
    <li>
      <svg viewBox="0 0 16 16" aria-label="Phone"><rect x="4" y="1" width="8" height="14" rx="1.5" fill="none" stroke="var(--green)" stroke-width="1.6"/><circle cx="8" cy="12.3" r=".9" fill="var(--green)"/></svg>
      0427 561 903
    </li>
    <li>
      <svg viewBox="0 0 16 16" aria-label="Fax"><rect x="4" y="1.5" width="8" height="4" fill="none" stroke="var(--green)" stroke-width="1.4"/><rect x="1.5" y="5.5" width="13" height="6" rx="1" fill="none" stroke="var(--green)" stroke-width="1.4"/><rect x="4" y="9.5" width="8" height="5" fill="#fff" stroke="var(--green)" stroke-width="1.4"/></svg>
      6457 2183
    </li>
    <li>
      <svg viewBox="0 0 16 16" aria-label="Email"><rect x="1.5" y="3.5" width="13" height="9" fill="none" stroke="var(--green)" stroke-width="1.4"/><path d="M1.5 3.5 L8 9 L14.5 3.5" fill="none" stroke="var(--green)" stroke-width="1.4"/></svg>
      marcus.k.diet@fernmail.com
    </li>
    <li>
      <svg viewBox="0 0 16 16" aria-label="Website"><circle cx="8" cy="8" r="6.5" fill="none" stroke="var(--green)" stroke-width="1.4"/><path d="M1.5 8 H14.5 M8 1.5 Q4 8 8 14.5 M8 1.5 Q12 8 8 14.5" fill="none" stroke="var(--green)" stroke-width="1.2"/></svg>
      www.brightfieldnutrition.com.au
    </li>
  </ul>

  <section class="locations">
    <h2 class="locations__title">Locations</h2>
    <ul class="locations__list">
      <li><svg viewBox="0 0 11 14" aria-hidden="true"><path d="M5.5 13.5 C2 9 1 7 1 5.2 A4.5 4.5 0 0 1 10 5.2 C10 7 9 9 5.5 13.5 Z" fill="var(--green)"/><circle cx="5.5" cy="5.2" r="1.6" fill="#fff"/></svg>Pinebrook Medical Centre</li>
      <li><svg viewBox="0 0 11 14" aria-hidden="true"><path d="M5.5 13.5 C2 9 1 7 1 5.2 A4.5 4.5 0 0 1 10 5.2 C10 7 9 9 5.5 13.5 Z" fill="var(--green)"/><circle cx="5.5" cy="5.2" r="1.6" fill="#fff"/></svg>North Corrin Health</li>
      <li><svg viewBox="0 0 11 14" aria-hidden="true"><path d="M5.5 13.5 C2 9 1 7 1 5.2 A4.5 4.5 0 0 1 10 5.2 C10 7 9 9 5.5 13.5 Z" fill="var(--green)"/><circle cx="5.5" cy="5.2" r="1.6" fill="#fff"/></svg>Hollis Medical</li>
      <li><svg viewBox="0 0 11 14" aria-hidden="true"><path d="M5.5 13.5 C2 9 1 7 1 5.2 A4.5 4.5 0 0 1 10 5.2 C10 7 9 9 5.5 13.5 Z" fill="var(--green)"/><circle cx="5.5" cy="5.2" r="1.6" fill="#fff"/></svg>Ashcombe Doctors Surgery</li>
    </ul>
  </section>
</article>

<article class="card card--back">
  <svg class="card__bands" viewBox="0 0 720 440" preserveAspectRatio="none" aria-hidden="true">
    <path d="M0 0 H110 Q40 200 50 440 H0 Z" fill="var(--green)"/>
    <path d="M0 0 H26 Q10 200 18 440 H0 Z" fill="var(--blue)"/>
    <path d="M720 0 H640 Q700 200 680 440 H720 Z" fill="var(--green)"/>
    <path d="M720 260 Q708 360 700 440 H720 Z" fill="var(--blue)"/>
  </svg>

  <div class="brand" style="left:90px; top:50px;">
    <span class="brand__dot"></span>
    <div>
      <div class="brand__name">Brightfield</div>
      <div class="brand__sub">Nutrition &amp; Dietetics</div>
    </div>
  </div>
  <div class="back__label">Appointment</div>

  <div class="divider" style="left:70px; right:80px; top:172px;"></div>

  <div class="fields">
    <div class="field">Name:<span class="field__line"></span></div>
    <div class="field">Appointment Date:<span class="field__line"></span></div>
    <div class="field">Appointment Time:<span class="field__line"></span></div>
    <div class="field">Appointment Location:<span class="field__line"></span></div>
  </div>
</article>

</body>
</html>
```